A parent Company needs a website as a leading diversified business in industrial Conglomerates in Af

Velkor Group is a private (Holding) limited liability company incorporated under the Companies Code, 1963 (Act 179) in November, 2013 to following the speedy growth in numbers of its current subsidiaries which has been founded several years ago with an emerging force to become one of the largest and a leading diversified business in industrial Conglomerates in Africa.
The Group which is 100% wholly owned indigenous Ghanaian Company focuses on provision of local, value-added products and services that meet the needs of the African population. The Group is headquartered in Accra, Ghana with interests across a range of sectors in Africa.
We are currently into Food & Beverage, Real Estate Development, Transportation, Health Care, Consumer Products Distribution, Agro Processing, Manufacturing, ICT, Exports & Import, and still counting.
In the next 3 years, we shall announce our ambitions to enter Ghana's largest Oil and Gas industry, playing a strategic role in the petroleum sector with strategic alliances, and help build Ghana's biggest and most important Energy sector in the country.
Inspired by billionaires Tom Prewitt, Harlan Voskel, and Emeka Ofodile, Velkor Group (Velkor Foundation) is committed to making a name for itself on the philanthropic circuit and has given away privately and still given to the cause to the needy in the society and some specific social causes in Ghana.
The company is managed by a 5 member board and a 2 member advisory experts who are non-board members.
The company has a vision, mission and it is guided by its core values.
We would like to see a designs that is very professional and looks corporate and can attract investors and partners. It must communicate financial safety and growth and must reflect our logo colors.

```html
<!DOCTYPE html>
<html lang="en">
<head>
<meta charset="utf-8">
<title>Velkor Group</title>
<link rel="stylesheet" href="https://fonts.googleapis.com/css2?family=Open+Sans:ital,wght@0,400;0,600;1,400&family=Ubuntu:wght@400;500&display=swap">
<style>
:root{
  --red:#d9161c;
  --red-bright:#ef2b2f;
  --blue:#1479c4;
  --blue-dark:#0d5ea3;
  --ink:#333;
  --muted:#8a8a8a;
  --nav:#333333;
  --nav-line:#4a4a4a;
  --foot:#3a3a3a;
  --foot-bar:#262626;
  --foot-text:#d6d6d6;
  --line:#dcdcdc;
}
*{box-sizing:border-box;margin:0;padding:0}
html,body{width:864px;height:1200px;overflow:hidden;background:#fff}
body{font-family:"Open Sans",Arial,sans-serif;color:var(--ink);position:relative}
.page{position:absolute;left:79px;top:16px;width:707px;height:1166px;background:#fff;border-top:2px solid var(--red);box-shadow:0 0 12px rgba(0,0,0,.12)}
.abs{position:absolute}
/* header */
.brand-mark{left:11px;top:18px;width:44px;height:44px;border-radius:50%;background:var(--blue)}
.brand-name{left:96px;top:33px;font-size:17px;font-weight:400;color:#3a3a3a;letter-spacing:.3px}
.brand-tag{left:95px;top:53px;font-size:9.5px;color:var(--red)}
.phone-icon{left:488px;top:27px;width:36px;height:36px}
.phone-number{left:530px;top:24px;font-family:"Ubuntu",sans-serif;font-size:24px;color:#555;letter-spacing:.3px}
.phone-note{left:530px;top:53px;font-size:12px;color:#444}
/* nav */
.nav{left:0;top:88px;width:707px;height:34px;background:var(--nav);display:flex}
.nav a{display:block;height:34px;line-height:34px;color:#fff;text-decoration:none;font-size:12.5px;text-align:center;border-right:1px solid var(--nav-line)}
.nav a.active{background:var(--red)}
.search{left:541px;top:95px;width:158px;height:22px;background:#f3f3f3;border:1px solid #bbb;font-size:8.5px;color:#999;padding:5px 6px}
.search svg{position:absolute;right:4px;top:3px}
/* hero */
.hero{left:0;top:122px;width:707px;height:337px;background:linear-gradient(100deg,#c9b49a 0%,#e8ddd0 30%,#d8c1a6 55%,#8a5c3e 80%,#5a3a28 100%)}
.welcome{left:15px;top:74px;width:330px;height:191px;background:rgba(255,255,255,.85)}
.welcome h1{position:absolute;left:10px;top:20px;font-family:"Ubuntu",sans-serif;font-weight:400;font-size:26px;color:#333;white-space:nowrap}
.welcome h1 span{color:var(--red)}
.welcome p{position:absolute;left:11px;top:68px;width:318px;font-size:10.4px;line-height:14.4px;color:#444;letter-spacing:-.15px}
.btn-more{position:absolute;left:11px;top:145px;width:160px;height:33px;background:linear-gradient(#1c86d0,var(--blue-dark));border-radius:2px;color:#fff;font-family:"Ubuntu",sans-serif;font-size:17px;line-height:33px;padding-left:19px}
.btn-more svg{position:absolute;right:17px;top:7px}
.dots{top:469px;height:3px;width:21px;background:#bbb}
/* services */
.section-title{left:0;width:707px;top:500px;text-align:center;font-family:"Ubuntu",sans-serif;font-weight:400;font-size:18px;color:var(--red)}
.card{top:542px;width:160px;height:219px;border:1px solid var(--line);background:#fff;box-shadow:0 6px 10px -6px rgba(0,0,0,.15)}
.card .thumb{position:absolute;left:8px;top:11px;width:144px;height:124px}
.card h3{position:absolute;left:7px;top:137px;font-family:"Ubuntu",sans-serif;font-weight:400;font-size:13.5px;color:var(--blue)}
.card p{position:absolute;left:8px;top:159px;width:146px;font-size:8.5px;line-height:12.8px;color:var(--muted)}
.card p a{color:var(--red);text-decoration:none}
.rule{left:0;top:784px;width:707px;height:1px;background:#e6e6e6}
/* about */
.h2{font-family:"Ubuntu",sans-serif;font-weight:400;font-size:16.5px;color:#333}
.about p{position:absolute;left:7px;width:460px;font-size:8.8px;line-height:12.8px;color:var(--muted)}
.about .read{position:absolute;left:7px;top:935px;font-size:9.5px;color:var(--red);font-style:italic;text-decoration:underline}
.access{left:499px;top:828px;width:176px;height:118px;border:1px solid var(--line)}
.field{position:absolute;left:6px;width:161px;height:19px;border:1px solid #ccc;font-size:8px;color:#666;padding:4px 7px}
.send{position:absolute;left:14px;top:85px;width:68px;height:23px;background:var(--red-bright);color:#fff;font-size:13px;text-align:center;line-height:23px}
/* footer */
.footer{left:0;top:973px;width:707px;height:155px;background:var(--foot)}
.footer h4{position:absolute;top:19px;font-family:"Ubuntu",sans-serif;font-weight:400;font-size:13.5px;color:#fff}
.links{position:absolute;left:8px;top:45px;font-size:9px;line-height:13.6px}
.links a{display:block;color:var(--foot-text);text-decoration:underline}
.what{position:absolute;left:178px;top:43px;font-size:9px;line-height:16px;color:var(--foot-text)}
.social{position:absolute;left:391px;top:43px;font-size:9px;line-height:17.2px;color:var(--foot-text)}
.social li,.contact li{list-style:none;position:relative;padding-left:19px}
.social li::before{content:"";position:absolute;left:1px;top:5px;width:8px;height:8px;background:#555}
.contact{position:absolute;left:542px;top:43px;font-size:9px;line-height:15.8px;color:var(--foot-text)}
.contact li.plain{padding-left:0}
.contact .num{position:absolute;left:55px}
.contact svg{position:absolute;left:0;top:4px}
.bottom{left:0;top:1128px;width:707px;height:36px;background:var(--foot-bar);font-size:9px;color:#e8e8e8}
.bottom span{position:absolute;top:11px}
</style>
</head>
<body>
<div class="page">
  <header>
    <div class="abs brand-mark"></div>
    <div class="abs brand-name">VELKOR GROUP</div>
    <div class="abs brand-tag">Steady Growth, Lasting Trust</div>
    <svg class="abs phone-icon" viewBox="0 0 36 36" aria-hidden="true">
      <path d="M9 6c-4 3-5 9-2 15s8 10 13 9l2-5-5-3-2 2c-3-2-5-5-6-8l2-2-2-6z" fill="none" stroke="var(--blue)" stroke-width="2.4"/>
      <path d="M22 8a8 8 0 0 1 5 7M24 3a13 13 0 0 1 8 12" fill="none" stroke="var(--blue)" stroke-width="2"/>
    </svg>
    <div class="abs phone-number">0800 555 0142</div>
    <div class="abs phone-note">Call Us Now For Free Quote</div>
  </header>

  <nav class="abs nav">
    <a class="active" style="width:89px">Home</a>
    <a style="width:117px">Food &amp; Beverages</a>
    <a style="width:104px">Transportation</a>
    <a style="width:106px">Agro Processing</a>
    <a style="width:100px">Manufacturing</a>
  </nav>
  <div class="abs search">Search here...
    <svg width="14" height="14" viewBox="0 0 14 14" aria-hidden="true"><circle cx="6" cy="6" r="4.2" fill="none" stroke="#aaa" stroke-width="1.5"/><path d="M9 9l4 4" stroke="#aaa" stroke-width="1.8"/></svg>
  </div>

  <section class="abs hero" role="img" aria-label="Business people taking notes at a meeting table">
    <div class="abs welcome">
      <h1>Welcome to <span>Velkor Group</span></h1>
      <p>Lorem Ipsum is simply dummy text of the printing and typesetting industry. Lorem Ipsum has been the industry's standard dummy text ever since the 1500s, when an unknown printer took a galley of type and scrambled it to make a type</p>
      <div class="btn-more">Learn More
        <svg width="20" height="20" viewBox="0 0 20 20" aria-hidden="true"><circle cx="10" cy="10" r="9.5" fill="#fff"/><path d="M5 10h9M10 6l4 4-4 4" fill="none" stroke="var(--blue-dark)" stroke-width="2"/></svg>
      </div>
    </div>
  </section>
  <div class="abs dots" style="left:310px"></div>
  <div class="abs dots" style="left:340px;background:var(--red)"></div>
  <div class="abs dots" style="left:371px"></div>

  <h2 class="abs section-title">Our Services</h2>

  <article class="abs card" style="left:8px">
    <div class="thumb" role="img" aria-label="Plates of food with a glass of beer" style="background:linear-gradient(135deg,#c98a3a,#e7c27a 50%,#b3651c)"></div>
    <h3>Food &amp; Beverages</h3>
    <p>Lorem ipsum dolor sit amet, consectetur adipisicing elit, sed do eiusmod tempor incididunt ut labore... <a>Read More</a></p>
  </article>
  <article class="abs card" style="left:184px">
    <div class="thumb" role="img" aria-label="Trucks driving along a snowy road" style="background:linear-gradient(180deg,#6f7c88,#b9c3cc 55%,#e5eaee)"></div>
    <h3>Transportation</h3>
    <p>Lorem ipsum dolor sit amet, consectetur adipisicing elit, sed do eiusmod tempor incididunt ut labore... <a>Read More</a></p>
  </article>
  <article class="abs card" style="left:360px">
    <div class="thumb" role="img" aria-label="Stethoscope resting on blue medical fabric" style="background:linear-gradient(135deg,#2a7fc2,#4fa3e0 55%,#1c5f99)"></div>
    <h3>Health &amp; Care</h3>
    <p>Lorem ipsum dolor sit amet, consectetur adipisicing elit, sed do eiusmod tempor incididunt ut labore... <a>Read More</a></p>
  </article>
  <article class="abs card" style="left:536px">
    <div class="thumb" role="img" aria-label="Builder working on a timber frame under blue sky" style="background:linear-gradient(160deg,#3f6fb5,#8fb2dd 50%,#c9a46b)"></div>
    <h3>Manufacturing</h3>
    <p>Lorem ipsum dolor sit amet, consectetur adipisicing elit, sed do eiusmod tempor incididunt ut labore... <a>Read More</a></p>
  </article>

  <div class="abs rule"></div>

  <section class="about">
    <h2 class="abs h2" style="left:7px;top:802px">About Us</h2>
    <p style="top:836px">Lorem ipsum dolor sit amet, consectetur adipisicing elit, sed do eiusmod tempor incididunt ut labore et dolore magna aliqua. Ut enim ad minim veniam, quis nostrud exercitation ullamco laboris nisi ut aliquip ex ea commodo consequat.</p>
    <p style="top:888px">Duis aute irure dolor in reprehenderit in voluptate velit esse cillum dolore eu fugiat nulla pariatur. Lorem ipsum dolor sit amet, consectetur adipisicing elit, sed do eiusmod quis nostrud exercitation ullamco laboris tempor incididunt ut labore et dolore magna aliqua.</p>
    <a class="read">Read More</a>
  </section>

  <h2 class="abs h2" style="left:500px;top:802px">Private Access</h2>
  <form class="abs access">
    <div class="field" style="top:12px">Name</div>
    <div class="field" style="top:38px">Email Address</div>
    <div class="send">SEND</div>
  </form>

  <footer class="abs footer">
    <h4 style="left:8px">Site Links</h4>
    <div class="links">
      <a>Home</a><a>Food &amp; Beverage</a><a>Real Estate Development</a><a>Transportation</a><a>Health Care</a><a>Consumer Products Distribution</a><a>Agro Processing</a>
    </div>
    <h4 style="left:177px">What We Do</h4>
    <div class="what">Lorem ipsum dolor sit amet<br>consectetur adipiscing elit,<br>Sed do euismod tempor<br>incidunt magna aliqua..</div>
    <h4 style="left:387px">Social Media</h4>
    <ul class="social"><li>Chatterly</li><li>Quipster</li><li>Circlenet</li><li>Lorem</li><li>Snapwall</li></ul>
    <h4 style="left:542px">Contact Us</h4>
    <ul class="contact">
      <li class="plain">Lorem</li>
      <li class="plain">Ipsum City<span class="num">0800-555-0101</span></li>
      <li class="plain">Dolor<span class="num" style="left:58px">0800-555-0102</span></li>
      <li><svg width="10" height="10" viewBox="0 0 10 10" aria-hidden="true"><path d="M2 1c-1.5 1-1.5 3 0 5s3.5 3.5 5.5 3l1-1.5-2-1.5-1 1c-1-.5-2-1.5-2.5-2.5l1-1-1-2z" fill="#ccc"/></svg>0800-555-0103</li>
      <li><svg width="10" height="10" viewBox="0 0 10 10" aria-hidden="true"><rect x="0.5" y="1.5" width="9" height="7" fill="none" stroke="#999"/><path d="M0.5 4h9" stroke="#999"/></svg>www.velkorgroup.example</li>
      <li><svg width="10" height="10" viewBox="0 0 10 10" aria-hidden="true"><rect x="0.5" y="2" width="9" height="6.5" fill="#999"/><path d="M0.5 2l4.5 3.5L9.5 2" fill="none" stroke="#3a3a3a"/></svg>info@velkorgroup.example</li>
    </ul>
  </footer>
  <div class="abs bottom">
    <span style="left:13px">Copyright © 2013 Northfield Studio - All Rights Reserved</span>
    <span style="left:497px">Terms &amp; Conditions</span>
    <span style="left:598px">|</span>
    <span style="left:617px">Privacy Policy</span>
  </div>
</div>
</body>
</html>
```